Business card for a new cabinet shop company named Veloran Cabinets for high end cabinets

Design a business card, thinking dark rich green with colours to speak of high end luxury ie; cream, gold, black possibly

Mitchell Tarrowby
Director Craftsman
Email: info@veloranjoinery-example.com.au
Instagram : @veloran.cabinets

```html
<!DOCTYPE html>
<html lang="en">
<head>
<meta charset="utf-8">
<title>Veloran Cabinets – Business Card</title>
<link rel="stylesheet" href="https://fonts.googleapis.com/css2?family=Montserrat:wght@400;500;800&display=swap">
<style>
  :root {
    --backdrop: #2b2b2b;
    --card-green: #07402b;
    --gold: #c8a862;
    --cream: #ffffff;
    --card-w: 540px;
    --card-h: 310px;
  }
  * { margin: 0; padding: 0; box-sizing: border-box; }
  html, body {
    width: 1200px;
    height: 694px;
    overflow: hidden;
    background: var(--backdrop);
    font-family: "Montserrat", sans-serif;
  }
  .stage {
    width: 1200px;
    height: 694px;
    display: flex;
    align-items: center;
    justify-content: center;
    gap: 40px;
  }
  .card {
    width: var(--card-w);
    height: var(--card-h);
    background: var(--card-green);
    border-radius: 22px;
    position: relative;
  }

  /* Front side */
  .card--front {
    display: flex;
    align-items: center;
    justify-content: center;
  }
  .brand {
    display: flex;
    align-items: center;
    gap: 14px;
  }
  .brand__dot {
    border: 2px solid var(--gold);
    border-radius: 50%;
    flex: none;
  }
  .brand__name {
    color: var(--gold);
    font-weight: 500;
    letter-spacing: 0.04em;
    white-space: nowrap;
  }
  .card--front .brand__dot { width: 40px; height: 40px; }
  .card--front .brand__name { font-size: 40px; }

  /* Back side */
  .card--back {
    display: flex;
    align-items: center;
    padding: 0 30px 0 34px;
  }
  .card--back .brand { width: 220px; gap: 9px; }
  .card--back .brand__dot { width: 20px; height: 20px; }
  .card--back .brand__name { font-size: 21px; }
  .divider {
    width: 1.5px;
    height: 120px;
    background: var(--gold);
    margin: 0 20px 0 8px;
    flex: none;
  }
  .contact { color: var(--cream); }
  .contact__name {
    color: var(--gold);
    font-weight: 800;
    font-size: 20px;
    line-height: 1.1;
  }
  .contact__title {
    font-size: 12.5px;
    margin: 3px 0 14px;
  }
  .contact__list { list-style: none; }
  .contact__item {
    display: flex;
    align-items: center;
    gap: 7px;
    font-size: 10.5px;
    line-height: 1.9;
    white-space: nowrap;
  }
  .contact__icon { width: 11px; height: 11px; flex: none; }
</style>
</head>
<body>
  <main class="stage">
    <section class="card card--front" aria-label="Card front">
      <div class="brand">
        <span class="brand__dot"></span>
        <span class="brand__name">Veloran Cabinets</span>
      </div>
    </section>

    <section class="card card--back" aria-label="Card back">
      <div class="brand">
        <span class="brand__dot"></span>
        <span class="brand__name">Veloran Cabinets</span>
      </div>
      <span class="divider"></span>
      <div class="contact">
        <p class="contact__name">Mitchell Tarrowby</p>
        <p class="contact__title">Director Craftsman</p>
        <ul class="contact__list">
          <li class="contact__item">
            <svg class="contact__icon" viewBox="0 0 12 12" aria-hidden="true">
              <rect x="0.5" y="2" width="11" height="8" fill="var(--gold)"/>
              <path d="M0.5 2 L6 6.5 L11.5 2" fill="none" stroke="var(--card-green)" stroke-width="1"/>
            </svg>
            info@veloranjoinery-example.com.au
          </li>
          <li class="contact__item">
            <svg class="contact__icon" viewBox="0 0 12 12" aria-hidden="true">
              <circle cx="6" cy="6" r="5.2" fill="none" stroke="var(--gold)" stroke-width="1.2"/>
              <ellipse cx="6" cy="6" rx="2.2" ry="5.2" fill="none" stroke="var(--gold)" stroke-width="1"/>
              <line x1="0.8" y1="6" x2="11.2" y2="6" stroke="var(--gold)" stroke-width="1"/>
            </svg>
            veloranjoinery-example.com.au
          </li>
          <li class="contact__item">
            <svg class="contact__icon" viewBox="0 0 12 12" aria-hidden="true">
              <circle cx="6" cy="6" r="4.5" fill="none" stroke="var(--gold)" stroke-width="1.4"/>
            </svg>
            @veloran.cabinets
          </li>
        </ul>
      </div>
    </section>
  </main>
</body>
</html>
```